BOLD & MINIMALIST DESIGN NEEDED

We want a very bold but minimalistic business card design that is impactful and utilizes both sides of the business card. Our current logo is included for your use.

We want bold fonts and good use of negative space. We don't want the logo to overpower the design.

Target Market(s)

Professionals who are building new commercial buildings.

Industry/Entity Type

Construction

Contact Information for Business Card

Name, Title, email, office phone, cell phone, website

Font styles to use
Serif
Sans Serif

Requirements
Must have
• Bold design!

```html
<!DOCTYPE html>
<html lang="en">
<head>
<meta charset="utf-8">
<title>Ridgeline Design + Build — Business Card</title>
<link href="https://fonts.googleapis.com/css2?family=Montserrat:wght@400;500;700;800&display=swap" rel="stylesheet">
<style>
  :root {
    --bg: #d1d1cd;
    --paper: #ffffff;
    --green: #82c12a;
    --green-deep: #6fa820;
    --ink: #1a1a1a;
    --shadow: rgba(0,0,0,0.22);
  }
  * { margin: 0; padding: 0; box-sizing: border-box; }
  html, body { width: 1200px; height: 801px; overflow: hidden; background: var(--bg); }
  body { font-family: "Montserrat", Arial, sans-serif; position: relative; }

  .card {
    position: absolute;
    top: 246px;
    width: 540px;
    height: 309px;
    box-shadow: 0 10px 24px var(--shadow);
  }
  .card--front { left: 40px; background: var(--paper); border-bottom: 4px solid var(--green); }
  .card--back { left: 620px; background: var(--green); overflow: hidden; }

  /* front */
  .brand {
    position: absolute;
    left: 46px; top: 118px;
    width: 210px;
    display: flex; align-items: center; gap: 10px;
  }
  .brand__dot { width: 18px; height: 18px; border-radius: 50%; background: var(--green); flex: none; }
  .brand__name {
    font-weight: 800; font-size: 25px; color: var(--ink);
    letter-spacing: 0.5px; line-height: 1.05;
  }
  .divider {
    position: absolute; left: 262px; top: 84px;
    width: 2px; height: 140px; background: var(--green);
  }
  .details { position: absolute; left: 286px; top: 82px; right: 20px; }
  .details__name {
    font-weight: 800; font-size: 22px; color: var(--green);
    letter-spacing: 1px; line-height: 1;
  }
  .details__title {
    font-weight: 500; font-size: 12px; color: var(--ink);
    letter-spacing: 1.5px; margin-top: 5px; margin-bottom: 18px;
  }
  .contact { list-style: none; }
  .contact__item {
    display: flex; align-items: center; gap: 8px;
    font-size: 12.5px; color: var(--ink); line-height: 1; margin-bottom: 7px;
  }
  .contact__icon { width: 12px; height: 12px; flex: none; }
  .contact__accent { color: var(--green); }

  /* back */
  .back__pattern {
    position: absolute; inset: 0;
    background: linear-gradient(160deg, #86c42e 0%, #7dbb27 55%, #74b022 100%);
  }
  .back__mark {
    position: absolute; right: 36px; bottom: 70px;
    display: flex; align-items: center; gap: 7px;
  }
  .back__dot { width: 10px; height: 10px; border-radius: 50%; background: var(--paper); }
  .back__name { font-weight: 800; font-size: 14px; color: var(--paper); letter-spacing: 0.5px; }
</style>
</head>
<body>

<section class="card card--front" aria-label="Business card front">
  <div class="brand">
    <span class="brand__dot"></span>
    <span class="brand__name">RIDGELINE<br>DESIGN + BUILD</span>
  </div>
  <div class="divider"></div>
  <div class="details">
    <h1 class="details__name">GRANT MERCER</h1>
    <p class="details__title">OWNER</p>
    <ul class="contact">
      <li class="contact__item">
        <svg class="contact__icon" viewBox="0 0 12 12"><path d="M2.5 1 L4.5 1 L5 3.5 L3.8 4.4 Q4.8 6.8 7.6 8.2 L8.5 7 L11 7.5 L11 9.5 Q11 11 9.5 11 Q1 10 1 2.5 Q1 1 2.5 1Z" fill="var(--green)"/></svg>
        (555) 214-0378
      </li>
      <li class="contact__item">
        <svg class="contact__icon" viewBox="0 0 12 12"><rect x="1" y="5" width="10" height="6" rx="1" fill="var(--green)"/><path d="M1 4 Q6 0 11 4 L9 5 L3 5Z" fill="var(--green)"/><circle cx="6" cy="8" r="1.5" fill="#fff"/></svg>
        (555) 214-0378
      </li>
      <li class="contact__item">
        <svg class="contact__icon" viewBox="0 0 12 12"><rect x="1" y="2.5" width="10" height="7" fill="none" stroke="var(--green)" stroke-width="1.2"/><path d="M1 2.5 L6 6.5 L11 2.5" fill="none" stroke="var(--green)" stroke-width="1.2"/></svg>
        ridgelinebuild@mail.com
      </li>
      <li class="contact__item">
        <svg class="contact__icon" viewBox="0 0 12 12"><circle cx="6" cy="6" r="5" fill="none" stroke="var(--green)" stroke-width="1.2"/><ellipse cx="6" cy="6" rx="2.2" ry="5" fill="none" stroke="var(--green)" stroke-width="1"/><path d="M1 6 H11" stroke="var(--green)" stroke-width="1"/></svg>
        www.<span class="contact__accent">ridgelinebuild</span>.com
      </li>
    </ul>
  </div>
</section>

<section class="card card--back" aria-label="Business card back">
  <div class="back__pattern" role="img" aria-label="Embossed repeating brand mark pattern in tonal green"></div>
  <div class="back__mark">
    <span class="back__dot"></span>
    <span class="back__name">RIDGELINE</span>
  </div>
</section>

</body>
</html>
```